Bright Harbor website redesign

We need a redesign for a website: mybrightharbor.example.

I already created a video going over what exactly is needed in the design.

See Video here: https://files.example.net/file/d/7xQpL2mR9vTz4KwB8nYcH3jDs6FgA1eU0/view?usp=sharing

Google Slide shown in Video: https://slides.example.net/presentation/d/9KP_Rtnwq3XbzmLeYc7VhJ2GoUd4Fs_PaiTe6q1kQ5Wr/edit?usp=sharing

Holidays in India so we did not get enough design entries or quality.

Target Market(s)

Dentistry

Industry/Entity Type

Dentistry

Number of Pages Required

1 page

Colors
0094D4
00A9DD
6FCCEA
C7EBF8
E9F6FB
00AB8E
00BBA5
67D7C9
C6EFE9
E9F9F6

Requirements
Must have
• See 13 min video link in description - shows what to do.

```html
<!DOCTYPE html>
<html lang="en">
<head>
<meta charset="utf-8">
<title>Bright Harbor Dental</title>
<link href="https://fonts.googleapis.com/css2?family=Poppins:wght@300;400;500;600;700&family=Montserrat:wght@400;500;600&display=swap" rel="stylesheet">
<style>
:root{
  --blue:#0094D4;
  --blue-bright:#00A9DD;
  --blue-soft:#6FCCEA;
  --blue-pale:#C7EBF8;
  --blue-mist:#E9F6FB;
  --teal:#00AB8E;
  --teal-bright:#00BBA5;
  --teal-soft:#67D7C9;
  --teal-pale:#C6EFE9;
  --teal-mist:#E9F9F6;
  --ink:#2f3b4c;
  --text:#55606e;
  --muted:#7a8290;
  --white:#ffffff;
}
*{margin:0;padding:0;box-sizing:border-box}
html,body{width:1200px;height:4178px;overflow:hidden;background:var(--white)}
body{position:relative;font-family:"Montserrat",sans-serif;color:var(--text)}
h1,h2,h3{font-family:"Poppins",sans-serif;font-weight:400;color:var(--ink)}
h2 b,h1 b{font-weight:700}

/* header */
.site-header{position:absolute;left:0;top:0;width:1200px;height:100px;background:var(--white);z-index:5}
.brand{position:absolute;left:90px;top:30px;display:flex;align-items:center;gap:10px}
.brand-dot{width:18px;height:18px;border-radius:50%;background:var(--teal)}
.brand-name{font-family:"Poppins",sans-serif;font-weight:600;font-size:24px;color:var(--blue)}
.top-phone{position:absolute;left:641px;top:6px;font-family:"Poppins",sans-serif;font-size:16px;font-weight:500;color:var(--blue);display:flex;align-items:center;gap:6px}
.top-btn{position:absolute;top:0;height:33px;color:#fff;font-size:12px;font-weight:600;display:flex;align-items:center;justify-content:center}
.top-btn.schedule{left:811px;width:154px;background:var(--blue)}
.top-btn.emergency{left:968px;width:152px;background:var(--teal)}
.nav a{position:absolute;top:57px;font-size:13.5px;color:var(--ink);text-decoration:none;white-space:nowrap}
.nav .caret{font-size:9px;color:var(--muted);margin-left:4px}
.nav-active{position:absolute;left:303px;top:97px;width:115px;height:3px;background:var(--teal)}

/* hero */
.hero{position:absolute;left:0;top:100px;width:1200px;height:700px;background:linear-gradient(160deg,var(--blue-bright) 0%,var(--blue) 55%,#0087c2 100%)}
.hero-art{position:absolute;left:640px;top:110px;width:480px;height:360px;border-radius:50%;background:radial-gradient(ellipse at center,rgba(255,255,255,.16),rgba(255,255,255,0) 70%)}
.hero h1{position:absolute;left:133px;top:146px;color:#fff;font-size:56px;line-height:58px;font-weight:300}
.hero h1 b{display:block;font-weight:700;color:#fff}
.hero .sub{position:absolute;left:135px;top:275px;color:#fff;font-family:"Poppins",sans-serif;font-size:24px;line-height:34px}
.btn-outline{position:absolute;left:130px;top:365px;width:257px;height:60px;border:3px solid #fff;border-radius:30px;color:#fff;font-size:15px;font-weight:600;display:flex;align-items:center;justify-content:center;letter-spacing:.3px}
.hero-wave{position:absolute;left:0;top:600px}
.scroll-btn{position:absolute;left:563px;top:638px;width:64px;height:64px;border-radius:50%;background:#fff;box-shadow:0 4px 14px rgba(0,0,0,.15);display:flex;align-items:center;justify-content:center}

/* welcome */
.welcome-photo{position:absolute;left:110px;top:752px;width:444px;height:444px;border-radius:50%;background:var(--blue-mist);box-shadow:0 0 20px rgba(0,0,0,.08)}
.welcome-photo .ring{position:absolute;left:10px;top:10px;width:424px;height:424px;border-radius:50%;border:3px solid var(--teal)}
.welcome-photo .img{position:absolute;left:22px;top:22px;width:400px;height:400px;border-radius:50%;background:linear-gradient(180deg,#6aa6dc 0%,#b9d4ea 35%,#a36a4f 60%,#5e8a3f 100%)}
.section-title{font-size:36px}
.rule{position:absolute;height:3px;background:var(--blue-bright)}
.welcome h2{position:absolute;left:589px;top:808px}
.welcome p{position:absolute;left:589px;width:490px;font-size:13.2px;line-height:24.5px;color:var(--text)}
.btn-dark{position:absolute;left:589px;top:1100px;width:163px;height:41px;border-radius:21px;background:var(--blue);color:#fff;font-size:13px;font-weight:600;display:flex;align-items:center;justify-content:center}

/* testimonials */
.band{position:absolute;left:0}
.center-title{position:absolute;left:0;width:1200px;text-align:center}
.review{position:absolute;top:1411px;width:296px;height:297px;background:#fff;border-radius:6px;box-shadow:0 2px 10px rgba(0,60,100,.08)}
.review .avatar{position:absolute;left:33px;top:24px;width:50px;height:50px;border-radius:50%;background:linear-gradient(135deg,var(--blue-soft),var(--blue))}
.review .who{position:absolute;left:97px;top:28px;font-size:13px;font-weight:600;color:var(--ink)}
.review .stars{position:absolute;left:95px;top:44px;color:#f2c12e;font-size:19px;letter-spacing:2px}
.review p{position:absolute;left:33px;top:90px;width:232px;font-size:12px;line-height:21.5px;color:var(--text)}
.review .source{position:absolute;right:26px;bottom:10px;font-family:"Poppins",sans-serif;font-weight:600;font-size:18px;color:var(--blue)}
.arrow{position:absolute;top:1540px}

/* services */
.service{position:absolute;width:220px;text-align:center}
.service .icon{margin:0 auto;width:92px;height:92px;border-radius:50%;background:#fff;box-shadow:0 3px 12px rgba(0,60,100,.1);display:flex;align-items:center;justify-content:center;color:var(--teal)}
.service.active .icon{background:var(--teal);color:#fff}
.service .label{margin-top:22px;font-family:"Poppins",sans-serif;font-weight:600;font-size:16px;color:var(--ink)}

/* team */
.member{position:absolute;top:2754px;width:270px;height:308px;background:#fff;box-shadow:0 2px 10px rgba(0,60,100,.08);text-align:center}
.member .photo{width:100%;height:238px;background:linear-gradient(180deg,var(--blue-mist),var(--blue-pale))}
.member .name{margin-top:14px;font-family:"Poppins",sans-serif;font-weight:600;font-size:15.5px;color:var(--ink)}
.member .role{margin-top:6px;font-size:13px;color:var(--text)}

/* excellence */
.excellence h2,.excellence h2 b{color:#fff}
.excellence .copy{position:absolute;left:260px;top:3380px;width:680px;text-align:center;color:#eaf7fc;font-size:13.5px;line-height:25px}
.excellence .walkin{position:absolute;left:0;top:3470px;width:1200px;text-align:center;color:#fff;font-family:"Poppins",sans-serif;font-size:21px}
.excellence .walkin b{font-weight:600;text-decoration:underline}
.btn-green{position:absolute;border-radius:28px;background:var(--teal);color:#fff;font-weight:600;display:flex;align-items:center;justify-content:center}
.btn-green.light{background:var(--teal-bright)}

/* footer */
.foot-title{position:absolute;top:3735px;font-family:"Poppins",sans-serif;font-size:22px;color:var(--ink)}
.foot-title b{font-weight:700}
.foot-rule{position:absolute;top:3776px;height:2px;background:var(--blue-bright)}
.contact-row{position:absolute;left:136px;display:flex;gap:12px;font-size:13px;line-height:21px;color:var(--ink)}
.hours{position:absolute;left:469px;top:3800px;font-size:13px;color:var(--ink);border-collapse:collapse}
.hours td{height:29.5px;padding:0}
.hours td:first-child{width:115px}
.map{position:absolute;left:762px;top:3795px;width:308px;height:184px;border:1px solid var(--blue-pale);background:linear-gradient(135deg,var(--blue-mist),var(--teal-mist))}
.foot-line{position:absolute;left:0;top:4055px;width:1200px;height:1px;background:var(--blue-pale)}
.foot-links a{position:absolute;top:4084px;font-size:12px;color:var(--ink);text-decoration:none}
.copyright{position:absolute;left:140px;top:4122px;font-size:10.5px;color:var(--muted)}
.social{position:absolute;top:4076px;width:24px;height:24px;border-radius:50%;background:var(--teal)}
</style>
</head>
<body>

<header class="site-header">
  <div class="brand"><span class="brand-dot"></span><span class="brand-name">Bright Harbor</span></div>
  <div class="top-phone">
    <svg width="20" height="20" viewBox="0 0 20 20"><circle cx="10" cy="10" r="10" fill="#0094D4"/><path d="M7 5.5l2 2.2-1 1.3c.6 1.3 1.6 2.3 2.9 2.9l1.3-1 2.2 2-1 1.6c-3.6-.3-7.3-4-7.6-7.6z" fill="#fff"/></svg>
    (555) 014-2290
  </div>
  <div class="top-btn schedule">Schedule Online</div>
  <div class="top-btn emergency">Emergency</div>
  <nav class="nav">
    <a style="left:303px">Meet Our Team<span class="caret">▼</span></a>
    <a style="left:440px">Services<span class="caret">▼</span></a>
    <a style="left:533px">Financing</a>
    <a style="left:633px">Testimonials</a>
    <a style="left:749px">New Patient Visit</a>
    <a style="left:897px">Specials</a>
    <a style="left:988px">Contact Us</a>
    <a style="left:1097px">Blog</a>
  </nav>
  <div class="nav-active"></div>
</header>

<section class="hero" role="img" aria-label="Blue-tinted photo of the clinic reception area">
  <div class="hero-art" role="img" aria-label="Large outline tooth and smile graphic"></div>
  <h1>Creating <b>Healthier Smiles</b></h1>
  <p class="sub">With Advanced Technology and<br>Affordable Treatment</p>
  <div class="btn-outline">BOOK AN APPOINTMENT</div>
</section>
<svg class="hero-wave" width="1200" height="200" viewBox="0 0 1200 200"><path d="M0 190 C 350 95 800 20 1200 118 L1200 200 L0 200Z" fill="#fff"/></svg>
<div class="scroll-btn"><svg width="22" height="24" viewBox="0 0 22 24"><path d="M11 2v19M3 13l8 8 8-8" stroke="#0094D4" stroke-width="2" fill="none" stroke-linecap="round"/></svg></div>

<section class="welcome">
  <div class="welcome-photo"><div class="ring"></div><div class="img" role="img" aria-label="Photo of the two-storey brick clinic building with its street sign"></div></div>
  <h2 class="section-title">Welcome to <b>Bright Harbor</b></h2>
  <div class="rule" style="left:589px;top:856px;width:141px"></div>
  <p style="top:880px">Your smile is our #1 priority. At Bright Harbor, we provide affordable and expert dental solutions. Whether you are looking for a family dentist or have any emergency such as needing a root canal in Marlow, we are here for you! We want to keep your teeth healthy inside and out. We don't just clean teeth and send you on your way, we want to get to know you.</p>
  <p style="top:1021px">We provide patients with the best experience you can find in all of Southern California. We provide a comfortable and friendly atmosphere</p>
  <div class="btn-dark">LEARN MORE</div>
</section>

<section class="testimonials">
  <svg class="band" style="top:1240px" width="1200" height="610" viewBox="0 0 1200 610"><path d="M0 90 Q600 -60 1200 70 L1200 520 Q600 680 0 500Z" fill="#E9F6FB"/></svg>
  <h2 class="center-title section-title" style="top:1322px;font-size:30px">What our Patients <b>Say About Us</b></h2>
  <div class="rule" style="left:553px;top:1374px;width:91px"></div>

  <svg class="arrow" style="left:78px" width="22" height="40" viewBox="0 0 22 40"><path d="M18 4L4 20l14 16" stroke="#0094D4" stroke-width="2" fill="none"/></svg>
  <svg class="arrow" style="left:1093px" width="22" height="40" viewBox="0 0 22 40"><path d="M4 4l14 16L4 36" stroke="#0094D4" stroke-width="2" fill="none"/></svg>

  <article class="review" style="left:131px">
    <div class="avatar" role="img" aria-label="Reviewer profile photo"></div>
    <div class="who">Dana K.</div><div class="stars">★★★★★</div>
    <p>“I am so happy I found Bright Harbor in Marlow. This is a long over due review since I have been seeing them for almost two years. They are always so friendly, understanding and empathetic when they have to deliver”</p>
    <div class="source">ratebook</div>
  </article>
  <article class="review" style="left:451px">
    <div class="avatar" role="img" aria-label="Reviewer profile photo"></div>
    <div class="who">Owen R.</div><div class="stars">★★★★★</div>
    <p>As most of us know going to the dentist isn't our favorite thing. But at this office the entire staff is super friendly, efficient, and professional. They start your appointment on time, unlike most offices.</p>
    <div class="source">ratebook</div>
  </article>
  <article class="review" style="left:769px">
    <div class="avatar" role="img" aria-label="Reviewer profile photo"></div>
    <div class="who">Priya L.</div><div class="stars">★★★★★</div>
    <p>Went here last July 2021 for the removal of my 1 impacted wisdom tooth. Office is clean, staff are courteous. Massage chair. Wait was quick. I chose the laughing gas and local anesthesia.</p>
    <div class="source">ratebook</div>
  </article>
</section>

<svg width="0" height="0" style="position:absolute">
  <defs>
    <symbol id="tooth" viewBox="0 0 40 40">
      <path d="M12 5c-5 0-8 4-7 10 1 5 3 7 3.5 12 .5 5 1.5 9 4 9s3-5 3.5-9c.3-2 1.2-3 4-3s3.7 1 4 3c.5 4 1 9 3.5 9s3.5-4 4-9C32 22 34 20 35 15c1-6-2-10-7-10-3 0-5 1.5-8 1.5S15 5 12 5z" fill="none" stroke="currentColor" stroke-width="1.8" stroke-linejoin="round"/>
    </symbol>
  </defs>
</svg>

<section class="services">
  <h2 class="center-title section-title" style="top:1874px">Our <b>Services</b></h2>
  <div class="rule" style="left:555px;top:1930px;width:91px"></div>

  <div class="service active" style="left:124px;top:1972px"><div class="icon"><svg width="44" height="44"><use href="#tooth"/></svg></div><div class="label">Dental Implants</div></div>
  <div class="service" style="left:373px;top:1972px"><div class="icon"><svg width="44" height="44"><use href="#tooth"/></svg></div><div class="label">Cosmetic Dentistry</div></div>
  <div class="service" style="left:605px;top:1972px"><div class="icon"><svg width="44" height="44"><use href="#tooth"/></svg></div><div class="label">Braces</div></div>
  <div class="service" style="left:847px;top:1972px"><div class="icon"><svg width="44" height="44"><use href="#tooth"/></svg></div><div class="label">Crowns</div></div>

  <div class="service" style="left:126px;top:2164px"><div class="icon"><svg width="44" height="44"><use href="#tooth"/></svg></div><div class="label">Bridge</div></div>
  <div class="service" style="left:368px;top:2164px"><div class="icon"><svg width="44" height="44"><use href="#tooth"/></svg></div><div class="label">Extractions</div></div>
  <div class="service" style="left:607px;top:2164px"><div class="icon"><svg width="44" height="44"><use href="#tooth"/></svg></div><div class="label">Gum Disease</div></div>
  <div class="service" style="left:844px;top:2164px"><div class="icon"><svg width="44" height="44"><use href="#tooth"/></svg></div><div class="label">Root Canal</div></div>

  <div class="service" style="left:129px;top:2364px"><div class="icon"><svg width="44" height="44"><use href="#tooth"/></svg></div><div class="label">Dentures</div></div>
  <div class="service" style="left:376px;top:2364px"><div class="icon"><svg width="44" height="44"><use href="#tooth"/></svg></div><div class="label">Emergency Dentistry</div></div>
  <div class="service" style="left:610px;top:2364px"><div class="icon"><svg width="44" height="44"><use href="#tooth"/></svg></div><div class="label">Veneers</div></div>
  <div class="service" style="left:838px;top:2364px"><div class="icon"><svg width="44" height="44"><use href="#tooth"/></svg></div><div class="label">Clear Aligners</div></div>
</section>

<section class="team">
  <svg class="band" style="top:2570px" width="1200" height="640" viewBox="0 0 1200 640"><path d="M0 90 Q600 -60 1200 80 L1200 640 L0 640Z" fill="#E9F9F6"/></svg>
  <h2 class="center-title section-title" style="top:2654px">Meet <b>Our Team</b></h2>
  <div class="member" style="left:170px"><div class="photo" role="img" aria-label="Portrait of the cosmetic dentist"></div><div class="name">Meet Dr. Aran Mehta</div><div class="role">Cosmetic Dentist</div></div>
  <div class="member" style="left:466px"><div class="photo" role="img" aria-label="Portrait of the endodontist"></div><div class="name">Dr. Leela Rao</div><div class="role">Endodontist</div></div>
  <div class="member" style="left:756px"><div class="photo" role="img" aria-label="Portrait of the general dentist"></div><div class="name">Meet Dr. Nisha Vora</div><div class="role">General Dentist</div></div>
</section>

<section class="excellence">
  <svg class="band" style="top:3110px" width="1200" height="576" viewBox="0 0 1200 576" role="img" aria-label="Blue-tinted photo of a dental treatment room">
    <defs><linearGradient id="deepBg" x1="0" y1="0" x2="1" y2="1"><stop offset="0" stop-color="#0094D4"/><stop offset="1" stop-color="#00AB8E"/></linearGradient></defs>
    <path d="M0 4 Q600 190 1200 30 L1200 576 L0 576Z" fill="url(#deepBg)"/>
  </svg>
  <h2 class="center-title section-title" style="top:3298px"><b>Committed to Excellence</b> in Oral Health Care</h2>
  <p class="copy">We provide patients with the best experience you can find in all of Southern California. We provide a comfortable and friendly atmosphere to shatter any fears you may have. We supply you with all the information on your dental health options so you can feel</p>
  <p class="walkin">We are avaliable for <b>Emergency and Walk-ins.</b></p>
  <div class="btn-green light" style="left:506px;top:3528px;width:214px;height:54px;font-size:14px;background:#fff;color:#0094D4">BOOK APPOINTMENT</div>
</section>

<footer>
  <h3 class="foot-title" style="left:136px"><b>Bright</b> Harbor</h3>
  <div class="foot-rule" style="left:136px;width:160px"></div>
  <div class="contact-row" style="top:3802px">
    <svg width="16" height="20" viewBox="0 0 16 20"><path d="M8 1a6 6 0 0 0-6 6c0 4.5 6 12 6 12s6-7.5 6-12a6 6 0 0 0-6-6z" fill="#0094D4"/><circle cx="8" cy="7" r="2.2" fill="#fff"/></svg>
    <span>48 Harbor Lane, Suite B<br>Marlow, CA 90000</span>
  </div>
  <div class="contact-row" style="top:3857px">
    <svg width="16" height="16" viewBox="0 0 16 16"><path d="M3 1.5l3 3-1.5 2c1 2 2.5 3.5 4.5 4.5l2-1.5 3 3-1.8 2C6.5 14.5 1.5 9.5 1 3.3z" fill="#0094D4"/></svg>
    <span>Call Us: (555) 014-2290</span>
  </div>
  <div class="contact-row" style="top:3886px">
    <svg width="16" height="14" viewBox="0 0 16 14"><rect x="1" y="2" width="14" height="10" fill="#0094D4"/><path d="M1 2l7 6 7-6" stroke="#fff" stroke-width="1.2" fill="none"/></svg>
    <span>hello@mybrightharbor.example</span>
  </div>
  <div class="btn-green" style="left:136px;top:3945px;width:206px;height:36px;font-size:12px;border-radius:18px">BOOK AN APPOINTMENT</div>

  <h3 class="foot-title" style="left:469px"><b>Office</b> Hours</h3>
  <div class="foot-rule" style="left:469px;width:165px"></div>
  <table class="hours">
    <tr><td>Monday:</td><td>10AM–7PM</td></tr>
    <tr><td>Tuesday:</td><td>10AM–7PM</td></tr>
    <tr><td>Wednesday:</td><td>9AM–6PM</td></tr>
    <tr><td>Thursday:</td><td>9AM–6PM</td></tr>
    <tr><td>Friday:</td><td>9AM–5PM</td></tr>
    <tr><td>Saturday:</td><td>9AM–1PM</td></tr>
  </table>

  <h3 class="foot-title" style="left:757px"><b>Our</b> Location</h3>
  <div class="foot-rule" style="left:757px;width:170px"></div>
  <div class="map" role="img" aria-label="Street map showing the clinic location with a pin"></div>

  <div class="foot-line"></div>
  <nav class="foot-links">
    <a style="left:140px">About Us</a>
    <a style="left:227px">Services</a>
    <a style="left:310px">Financing</a>
    <a style="left:399px">Testimonials</a>
    <a style="left:504px">New Patient Visit</a>
    <a style="left:635px">Specials</a>
    <a style="left:717px">Contact Us</a>
    <a style="left:814px">Blog</a>
  </nav>
  <p class="copyright">2021 Bright Harbor &nbsp;|&nbsp; All Rights Reserved</p>
  <span class="social" style="left:932px"></span>
  <span class="social" style="left:962px"></span>
  <span class="social" style="left:991px"></span>
  <span class="social" style="left:1020px"></span>
  <span class="social" style="left:1049px"></span>
</footer>

</body>
</html>
```